Desert Basin Company Brochure

**** UPDATE 2-8-2014 ****

Size should be 11" X 17" or larger (tri or bi fold).

We're going to let the contest run it's full duration to allow for more time spent on designs.

No black backgrounds.

Consideration should be given to having the text be easy to read and in a nice, organized format.

*****************************

We're looking for an eye-catching, colorful brochure that will explain what we do, who we are... and what sets us apart from the competition.

Our company provides swimming pool service, repair, and custom renovations throughout the Phoenix, Arizona metropolitan area. These brochures will be hand-delivered to each prospective customer we visit.

The brochure will include images of our work, product logos, and a unique design that separates our company apart from the rest.

The brochure should be tri-fold. Although, if a designer wants to (or has better ideas) for a different lay-out, then we're open to seeing what can be done.

Colors we like: Blue, White, Silver, Copper, Green (accent color)

We like designs that are unique/different. Professional. Creative. Sleek. Sexy. Custom. We don't want the brochure to be "pretentious". We'd like for these brochures to leave a lasting impression with our prospective clients... and hopefully earn us more business.

We don't want the brochure to be too wordy, however if the designer feels we need to cut back (or add), let us know.

Our motto is "Every Ripple Counts".

You can view some of our projects, and what we're about either at our website (tidewellpools.example), Friendline (www.facebook/tidewellpools), or Searchly+ (https://plus.google.com/+Tidewellpools). Thank you!

- Print-

(Front) Logo

Service - Repair - Renovation
555-347-9180
tidewellpools.example
service@tidewellpools.example
Like Us On Friendline! Friendline LOGO
Searchly Plus LOGO

(Body) Why Choose Us?

Thank you for the opportunity for our company to become your pool service provider!

We’re committed to providing the best customer service possible! At the end of the day you want your pool to be clean, clear, operational, and for your service provider to be available when you need them!

We’re licensed with the Sonoran Trades Licensing Board, Bonded, and Fully Insured.
A+ reviews with the Fair Merchant Council, Corra's Picks, Brivo, Olt, Friendline, and Searchly!
All technicians are employees... not sub-contractors! Our employees are hard working, dependable, professional, and expected to follow our strict protocol for servicing your pool.
Flat-fee service rates! Any additional equipment repairs, maintenance, or chemical implementations are directly authorized by you!
No contracts! Our Service Level Agreement Form allows you to select your desired level of authorization for equipment repairs, filter maintenance, and extra chemical implementation programs.
Our uniformed technicians arrive in distinctive, clean GPS-tracked company trucks.
We leave detailed service slips after each service visit. In addition, all service visit information is electronically recorded and stored.
Easy, online account management to view and pay invoices or authorize estimates.
Invoices, estimates, questions, pictures, and video are communicated via e-mail!
Free service calls to diagnose equipment issues outside of our normal service.
10% Service Client Discount for all repairs and replacement items.
Tidewell Pools knows the importance of communication! We’re available by phone, email, or text all days of the week.

(Body) Our Methodology

We believe in 5 important factors in maintaining a clean, clear, and operational pool...

Good, Clean Water! Our local water supply contains high amounts of minerals. Pool chemicals add to this problem in a short amount of time. Our philosophy is to use the least amount of chemicals possible to achieve optimal water balance.
Efficient Water Flow! The invention of variable-speed pumps has enabled the ability to "dial in" proper water flow... while driving down energy costs.
Proper Filtration! Today’s high-capacity cartridge filters provide great filtration, save on wasted water from backwashing sand filters, and eliminate the need for water flow-restricting backwash valves.
Functioning Cleaning System! Having a working automatic cleaning system is vital in keeping the pool surface clean of debris and dirt... and free of staining.
A Dependable And Professional Pool Maintenance Technician! Our job is to not only oversee all of the items listed above... but to make sure your pool is in the best condition possible!

(Body) Equipment Repair & Installation

We’re educated on all phases of swimming pool equipment repair and installation... with a focus on energy-efficiency and optimum performance!

We’re an VRE & MQW Authorized Installer of variable-speed pool pumps. VRE & MQW trust us to properly install and calibrate all variable-speed pumps. We've been equipped to handle the new industry standards on variable-speed pumps since Arizona law went into effect January 1st, 2011.
We’re experts at acid washes and erasing the mineral build-up off of waterlines. All work is done in-house with our customized cleaning rig and trailer.
Heating systems. New efficiency standards have made installation and operation more affordable than ever.
Remote control automation systems. Technology now allows the user to easily view and control their entire pool system via a remote home computer, tablet, or phone!
Brilliant, color-changing LED lighting for pools and spas! The benefits of LED include brighter and broader displays... while lasting much longer than your typical light bulbs.
Salt systems provide a soft-water experience! In addition to the benefit of better feeling water, salt systems generate plenty of chlorine to keep your pool sanitized.

(Body) About Us

A native to Phoenix, Daniel Harrow founded Tidewell Pools in 2000. Our company was built from the ground up by way of hard work, word of mouth, and determination. Our company will always remain firmly grounded, and continue to develop systems that put our customers first!

Our philosophy is to treat every pool as if it were our own, run an efficient and organized business, and care for our employees.

Tidewell Pools is a yearly, proud contributor to the Saguaro Youth Clinic Swim Smart Day. Please educate and watch all children around water... every accident can be avoided.

(Back) Contact Us

Office: 555-347-9180 | Fax: 555-347-9186 | Email: service@tidewellpools.example
tidewellpools.example

Office / Warehouse Location
41572 West 8th Street, Suite 4
Phoenix, Arizona 85999
(NW of 8th Street & Mesquite Ridge Road)

AZ ROC: 731150, 731151, 731152, 604378

Target Market(s)

We target a market of pool owners, which typically have more disposable income.

30 - 75 years old.

Our clients range from first-time home buyers, self-employed, business professionals, doctors, landlords, thousandaires, millionaires.

Industry/Entity Type

Pool Service

Font styles to use
Serif

Colors
0355a3
cfdfed
ffffff
3176b5
eaf1f7

Requirements
Must have
• Must use provided images. We've included a few pool pictures, and will let you decide which ones to incorporate throughout the brochure.

Logos Used:
Tidewell Pools
Hydrovel
FMC
Corra's Picks
VRE
MQW
Saguaro Youth Clinic
Searchly+
Friendline

Image pic of some of our trucks.

Nice to have
• Equipment images worked in.
Should not have
• Cartoonish fonts or design. No "Love" hearts!!

```html
<!DOCTYPE html>
<html lang="en">
<head>
<meta charset="utf-8">
<title>Tidewell Pools — Tri-fold Brochure Interior</title>
<link rel="stylesheet" href="https://fonts.googleapis.com/css2?family=Open+Sans:wght@400;600;700&family=Oswald:wght@500;600&display=swap">
<style>
  :root {
    --page-bg: #e6e6e6;
    --panel-bg: #eaf1f7;
    --panel-edge: #cfdfed;
    --band-blue: #0355a3;
    --label-blue: #0355a3;
    --label-accent: #3176b5;
    --text-body: #1c3550;
    --text-white: #ffffff;
    --water-deep: #1f5f70;
    --water-mid: #3f8fa0;
    --water-light: #8fd0dc;
    --stone: #b9ab96;
    --stone-dark: #6d5f4f;
    --sky: #9cb8d4;
    --ground: #a99a82;
  }
  * { box-sizing: border-box; margin: 0; padding: 0; }
  html, body { width: 1200px; height: 800px; overflow: hidden; }
  body {
    background: var(--page-bg);
    font-family: "Open Sans", Arial, sans-serif;
    position: relative;
  }
  .brochure {
    position: absolute;
    left: 90px; top: 50px;
    width: 1020px; height: 700px;
    display: grid;
    grid-template-columns: 340px 340px 340px;
    box-shadow: 0 18px 40px rgba(0,0,0,0.22);
  }
  .panel {
    position: relative;
    background: var(--panel-bg);
    color: var(--text-body);
    padding: 20px 20px 30px;
    font-size: 9px;
    line-height: 1.35;
  }
  .panel + .panel { border-left: 1px solid var(--panel-edge); }
  .panel::after {
    content: ""; position: absolute; left: 0; right: 0; bottom: 0;
    height: 12px; background: var(--band-blue);
  }
  .section-label {
    display: inline-block;
    background: var(--label-blue);
    color: var(--text-white);
    font-family: "Oswald", "Arial Narrow", sans-serif;
    font-weight: 600;
    font-size: 10.5px;
    letter-spacing: 0.06em;
    text-transform: uppercase;
    padding: 2px 30px 2px 10px;
    margin: 0 0 7px -4px;
  }
  .panel p { margin-bottom: 5px; }
  .bullet-list { list-style: none; }
  .bullet-list li { position: relative; padding-left: 9px; margin-bottom: 1px; }
  .bullet-list li::before { content: "•"; position: absolute; left: 0; color: var(--label-accent); }
  .photo-row {
    position: absolute; left: 20px; right: 20px; bottom: 28px;
    display: grid; grid-template-columns: 1fr 1fr; gap: 14px;
  }
  .photo {
    height: 100px;
    border: 2px solid var(--panel-edge);
  }
  .photo--natural-pool {
    background: linear-gradient(180deg, var(--sky) 0%, #c7d6e4 38%, var(--ground) 55%, var(--water-mid) 75%, var(--stone-dark) 100%);
  }
  .photo--resort-pool {
    background: linear-gradient(180deg, #6a5a48 0%, #b29a7c 35%, var(--water-light) 55%, #2f86b8 80%, #c8b9a0 100%);
  }
  .panel--feature { padding: 0; overflow: hidden; }
  .feature-photo {
    position: absolute; inset: 0 0 12px 0;
    background:
      radial-gradient(ellipse 60% 40% at 85% 30%, var(--stone) 0%, rgba(185,171,150,0) 70%),
      linear-gradient(160deg, var(--water-light) 0%, var(--water-mid) 35%, var(--water-deep) 65%, var(--stone-dark) 100%);
  }
  .feature-title {
    position: absolute; right: 14px; bottom: 52px;
    display: flex; flex-direction: column; align-items: flex-end; gap: 6px;
  }
  .feature-title span {
    background: var(--label-blue);
    color: var(--text-white);
    font-family: "Oswald", "Arial Narrow", sans-serif;
    font-weight: 600;
    font-size: 29px;
    line-height: 1.15;
    letter-spacing: 0.02em;
    padding: 2px 10px;
  }
  .panel--right .section-label.second { margin-top: 6px; }
</style>
</head>
<body>
  <main class="brochure">
    <section class="panel panel--left">
      <h2 class="section-label">Why Choose Us?</h2>
      <p>Thank you for the opportunity for our company to become your pool service provider!</p>
      <p>We’re committed to providing the best customer service possible! At the end of the day you want your pool to be clean, clear, operational, and for your service provider to be available when you need them!</p>
      <ul class="bullet-list">
        <li>We’re licensed with the Sonoran Trades Licensing Board, Bonded, and Fully Insured.</li>
        <li>A+ reviews with the Fair Merchant Council, Corra's Picks, Brivo, Olt, Friendline, and Searchly!</li>
        <li>All technicians are employees... not sub-contractors! Our employees are hard working, dependable, professional, and expected to follow our strict protocol for servicing your pool.</li>
        <li>Flat-fee service rates! Any additional equipment repairs, maintenance, or chemical implementations are directly authorized by you!</li>
        <li>No contracts! Our Service Level Agreement Form allows you to select your desired level of authorization for equipment repairs, filter maintenance, and extra chemical implementation programs.</li>
        <li>Our uniformed technicians arrive in distinctive, clean GPS-tracked company trucks.</li>
        <li>We leave detailed service slips after each service visit. In addition, all service visit information is electronically recorded and stored.</li>
        <li>Easy, online account management to view and pay invoices or authorize estimates.</li>
        <li>Invoices, estimates, questions, pictures, and video are communicated via e-mail!</li>
        <li>Free service calls to diagnose equipment issues outside of our normal service.</li>
        <li>10% Service Client Discount for all repairs and replacement items.</li>
        <li>Tidewell Pools knows the importance of communication! We’re available by phone, email, or text all days of the week.</li>
      </ul>
      <div class="photo-row">
        <div class="photo photo--natural-pool" role="img" aria-label="Photo of a natural rock-edged pool under a desert sky"></div>
        <div class="photo photo--resort-pool" role="img" aria-label="Photo of a bright blue backyard pool with a stone deck"></div>
      </div>
    </section>

    <section class="panel panel--feature">
      <div class="feature-photo" role="img" aria-label="Photo of a rock waterfall spilling into a clear turquoise pool"></div>
      <h1 class="feature-title"><span>ANOTHER TITLE</span><span>GOES HERE!</span></h1>
    </section>

    <section class="panel panel--right">
      <h2 class="section-label">Our Methodology</h2>
      <p>We believe in 5 important factors in maintaining a clean, clear, and operational pool...</p>
      <ul class="bullet-list">
        <li>Good, Clean Water! Our local water supply contains high amounts of minerals. Pool chemicals add to this problem in a short amount of time. Our philosophy is to use the least amount of chemicals possible to achieve optimal water balance.</li>
        <li>Efficient Water Flow! The invention of variable-speed pumps has enabled the ability to "dial in" proper water flow... while driving down energy costs.</li>
        <li>Proper Filtration! Today’s high-capacity cartridge filters provide great filtration, save on wasted water from backwashing sand filters, and eliminate the need for water flow-restricting backwash valves.</li>
        <li>Functioning Cleaning System! Having a working automatic cleaning system is vital in keeping the pool surface clean of debris and dirt... and free of staining.</li>
        <li>A Dependable And Professional Pool Maintenance Technician! Our job is to not only oversee all of the items listed above... but to make sure your pool is in the best condition possible!</li>
      </ul>
      <h2 class="section-label second">Equipment Repair &amp; Installation</h2>
      <p>We’re educated on all phases of swimming pool equipment repair and installation... with a focus on energy-efficiency and optimum performance!</p>
      <ul class="bullet-list">
        <li>We’re an VRE &amp; MQW Authorized Installer of variable-speed pool pumps. VRE &amp; MQW trust us to properly install and calibrate all variable-speed pumps. We've been equipped to handle the new industry standards on variable-speed pumps since Arizona law went into effect January 1st, 2011.</li>
        <li>We’re experts at acid washes and erasing the mineral build-up off of waterlines. All work is done in-house with our customized cleaning rig and trailer.</li>
        <li>Heating systems. New efficiency standards have made installation and operation more affordable than ever.</li>
        <li>Remote control automation systems. Technology now allows the user to easily view and control their entire pool system via a remote home computer, tablet, or phone!</li>
        <li>Brilliant, color-changing LED lighting for pools and spas! The benefits of LED include brighter and broader displays... while lasting much longer than your typical light bulbs.</li>
        <li>Salt systems provide a soft-water experience! In addition to the benefit of better feeling water, salt systems generate plenty of chlorine to keep your pool sanitized.</li>
      </ul>
    </section>
  </main>
</body>
</html>
```